Road Construction Company needs business cards

We would like a new business card designed for our business.

We're a road construction company based in Qld, Australia.

Can the business card please have the following information on it.

Name: Warren Halbeck
Position: General Manager
Phone: 0472 915 348
Email: Warren.halbeck@tovrin.com.au
Address: 87 Marrow Ave, Pendlebay, QLD, 4023
Website: www.tovrin.com.au

Visually we'd like the card to be professional and simple.

Attached is our logo.

Our website is www.tovrin.com.au

Target Market(s)

Men aged 25-60

Contact Information for Business Card

As listed in project description

Font styles to use
Serif

Requirements
Must have
• Large logo on back of card

```html
<!DOCTYPE html>
<html lang="en">
<head>
<meta charset="utf-8">
<title>Tovrin Business Card</title>
<link rel="stylesheet" href="https://fonts.googleapis.com/css2?family=Montserrat:wght@400;600;800&display=swap">
<style>
  :root {
    --bg: #3a3a3a;
    --paper: #ffffff;
    --brand-dark: #0d56a6;
    --brand-light: #2a9fd9;
    --ink: #1b1b1b;
  }
  html, body {
    margin: 0;
    padding: 0;
    width: 1200px;
    height: 1059px;
    overflow: hidden;
    background: var(--bg);
    font-family: "Montserrat", Arial, sans-serif;
  }
  .canvas { position: relative; width: 1200px; height: 1059px; }
  .card {
    position: absolute;
    width: 690px;
    height: 392px;
    border-radius: 18px;
    overflow: hidden;
  }
  .card--front { left: 255px; top: 100px; background: var(--paper); }
  .card--back { left: 255px; top: 538px; background: var(--brand-dark); }

  .wordmark {
    position: absolute;
    left: 0; right: 0;
    text-align: center;
    font-weight: 800;
    letter-spacing: 2px;
    text-transform: uppercase;
    line-height: 1;
  }
  .card--front .wordmark { top: 76px; font-size: 66px; color: var(--brand-dark); }
  .card--back .wordmark { top: 154px; font-size: 76px; color: var(--paper); }

  .person {
    position: absolute;
    right: 372px;
    top: 218px;
    text-align: right;
  }
  .person__name { margin: 0; font-size: 27px; font-weight: 600; line-height: 1.1; white-space: nowrap; }
  .person__first { color: var(--brand-dark); }
  .person__last { color: var(--brand-light); }
  .person__role { margin: 2px 0 0; font-size: 16px; color: var(--ink); }

  .divider {
    position: absolute;
    left: 343px; top: 213px;
    width: 2px; height: 60px;
    background: var(--brand-dark);
  }

  .contacts {
    position: absolute;
    left: 372px; top: 204px;
    margin: 0; padding: 0;
    list-style: none;
  }
  .contacts li {
    display: flex;
    align-items: center;
    height: 25.5px;
    font-size: 15.5px;
    color: var(--ink);
    white-space: nowrap;
  }
  .contacts svg { width: 13px; height: 13px; margin-right: 9px; fill: var(--brand-dark); flex: none; }

  .address-band {
    position: absolute;
    left: 0; right: 0;
    top: 322px; height: 26px;
    background: var(--brand-dark);
    color: var(--paper);
    font-size: 15px;
    line-height: 26px;
    text-align: center;
  }
</style>
</head>
<body>
<div class="canvas">
  <section class="card card--front">
    <div class="wordmark">Tovrin</div>

    <div class="person">
      <h1 class="person__name"><span class="person__first">Warren</span> <span class="person__last">Halbeck</span></h1>
      <p class="person__role">General Manager</p>
    </div>

    <div class="divider"></div>

    <ul class="contacts">
      <li>
        <svg viewBox="0 0 24 24" aria-hidden="true"><path d="M6.6 10.8a15.1 15.1 0 0 0 6.6 6.6l2.2-2.2a1 1 0 0 1 1-.25 11.4 11.4 0 0 0 3.6.57 1 1 0 0 1 1 1V20a1 1 0 0 1-1 1A17 17 0 0 1 3 4a1 1 0 0 1 1-1h3.5a1 1 0 0 1 1 1c0 1.25.2 2.45.57 3.57a1 1 0 0 1-.25 1z"/></svg>
        0472 915 348
      </li>
      <li>
        <svg viewBox="0 0 24 24" aria-hidden="true"><path d="M2 5h20v2l-10 6L2 7z"/><path d="M2 9l10 6 10-6v10H2z"/></svg>
        Warren.halbeck@tovrin.com.au
      </li>
      <li>
        <svg viewBox="0 0 24 24" aria-hidden="true"><path d="M12 2a10 10 0 1 0 0 20 10 10 0 0 0 0-20zm7.9 9h-3.4a15 15 0 0 0-1.3-5.6A8 8 0 0 1 19.9 11zM12 4c1 1.2 2.2 3.7 2.5 7h-5C9.8 7.7 11 5.2 12 4zM8.8 5.4A15 15 0 0 0 7.5 11H4.1a8 8 0 0 1 4.7-5.6zM4.1 13h3.4a15 15 0 0 0 1.3 5.6A8 8 0 0 1 4.1 13zM12 20c-1-1.2-2.2-3.7-2.5-7h5c-.3 3.3-1.5 5.8-2.5 7zm3.2-1.4a15 15 0 0 0 1.3-5.6h3.4a8 8 0 0 1-4.7 5.6z"/></svg>
        www.tovrin.com.au
      </li>
    </ul>

    <div class="address-band">87 Marrow Ave, Pendlebay, QLD, 4023</div>
  </section>

  <section class="card card--back">
    <div class="wordmark">Tovrin</div>
  </section>
</div>
</body>
</html>
```